Vehicle Rental Hire in the Algarve - Portugal

We are opening a Vehicle Rental company in the Algarve - Portugal - this will attract both locals and Tourists visiting. So we want this website to capture the beautiful location we will be set in, along with the familiarity of a vehicle rental company. And to keep a colour scheme in Line with out Logo. We are Quenmira Vehicle Rental.

Industry/Entity Type

Vehicle Rental

Number of Pages Required

1 page

Requirements
Must have
• must be professional, and simple to use navigation bar - must also have a "make a reservation" box - similar to the screenshot attached - Under our logo it must read "Vehicle Rental"
Nice to have
• It needs to be in a colour scheme that fits in with our logo

```html
<!DOCTYPE html>
<html lang="en">
<head>
<meta charset="utf-8">
<title>Quenmira Vehicle Rental</title>
<link href="https://fonts.googleapis.com/css2?family=Poppins:wght@300;400;500;600;700&display=swap" rel="stylesheet">
<style>
:root{
  --blue:#1a12e0;
  --red:#c8362e;
  --ink:#1b1b1b;
  --muted:#4a4a4a;
  --soft:#eff0fa;
  --white:#ffffff;
  --panel:rgba(20,16,18,.82);
}
*{box-sizing:border-box;margin:0;padding:0}
html,body{width:1200px;height:2832px;overflow:hidden}
body{font-family:'Poppins',sans-serif;color:var(--ink);background:var(--white);position:relative}
.abs{position:absolute}
.topbar{top:0;left:0;width:1200px;height:55px;font-size:14px;color:var(--blue)}
.topbar .call{left:112px;top:20px;display:flex;align-items:center;gap:8px}
.topbar .mail{right:110px;top:20px;display:flex;align-items:center;gap:8px}
.nav{top:55px;left:0;width:1200px;height:78px;background:var(--blue)}
.nav a{position:absolute;top:31px;color:var(--white);text-decoration:none;font-size:16px;font-weight:500}
.nav .cta{top:18px;left:988px;width:136px;height:42px;background:var(--white);color:var(--blue);border-radius:21px;text-align:center;line-height:42px;font-weight:600}
.brand{left:506px;top:10px;width:188px;height:188px;border-radius:50%;background:var(--white);display:flex;align-items:center;justify-content:center;text-align:center;z-index:3}
.brand span{color:var(--blue);font-weight:600;font-size:21px;line-height:1.2;width:140px}
.hero{top:133px;left:0;width:1200px;height:637px;background:linear-gradient(180deg,#3b5a7a 0%,#6f7f88 30%,#8a6e58 55%,#7a5f47 100%)}
.reserve{left:111px;top:133px;width:351px;height:637px;background:var(--panel);color:var(--white);padding:24px 18px}
.reserve h2{font-size:21px;font-weight:500;padding-bottom:16px;border-bottom:1px solid rgba(255,255,255,.6)}
.reserve label{position:absolute;left:18px;font-size:14px;color:#d9d3d3}
.field{position:absolute;height:38px;background:var(--white);border-radius:4px;color:#aaa;font-size:13px;line-height:38px;padding-left:13px}
.field.sel::after{content:"›";position:absolute;right:12px;color:#555;font-size:18px}
.reserve .same{position:absolute;left:43px;top:188px;font-size:14px;color:var(--white)}
.search{position:absolute;left:19px;top:562px;width:313px;height:43px;background:var(--blue);border:1px solid #fff;border-radius:5px;color:var(--white);text-align:center;line-height:42px;font-weight:600;font-size:14px}
.welcome{right:110px;top:218px;text-align:right;color:var(--white);z-index:4}
.welcome .pre{font-size:27px;font-weight:600}
.welcome h1{font-size:40px;font-weight:700;margin-top:6px;white-space:nowrap}
.welcome p{font-size:16px;font-weight:600;line-height:31px;margin-top:14px;white-space:nowrap}
.welcome .btn{display:inline-block;margin-top:22px;width:153px;height:60px;border-radius:30px;background:var(--white);color:var(--blue);font-weight:600;font-size:19px;line-height:60px;text-align:center}
.fleetshot{left:577px;top:532px;width:621px;height:336px;border-radius:40px 40px 120px 60px;background:linear-gradient(135deg,#e8e8ea 0%,#b9bcc2 40%,#2f6fc9 65%,#1c4e9e 100%);z-index:2}
.title{width:1200px;left:0;text-align:center;font-size:32px;font-weight:700;color:var(--blue)}
.title em{font-style:normal;color:var(--red)}
.about p{left:150px;width:900px;text-align:center;font-size:14.5px;font-weight:300;line-height:31px;color:#333}
.pill{background:var(--blue);color:var(--white);border-radius:26px;text-align:center;font-weight:600;font-size:18px}
.vehicles{top:1328px;left:0;width:1200px;height:478px;background:var(--soft)}
.card{top:1435px;width:291px;height:298px;background:var(--white);box-shadow:0 2px 8px rgba(0,0,0,.12);border-radius:4px;overflow:hidden}
.card .ph{height:236px}
.card h3{text-align:center;font-size:16px;font-weight:600;margin-top:22px}
.arrow{top:1570px;width:28px;height:28px;border-radius:50%;background:#111;color:#fff;text-align:center;line-height:26px;font-size:20px}
.avatar{border-radius:50%}
.quote{font-size:200px;font-weight:700;color:#d8d8d8;line-height:1}
.testi{left:0;width:1220px;text-align:center}
.footer{top:2405px;left:0;width:1200px;height:427px;background:var(--blue);color:var(--white)}
.footer h4{position:absolute;font-size:20px;font-weight:600}
.footer ul{position:absolute;list-style:none;font-size:15px}
.footer li{height:34px;display:flex;align-items:center;gap:10px}
.dot{width:13px;height:13px;border-radius:50%;background:var(--white);display:inline-block;position:relative}
.dot::after{content:"";position:absolute;left:3px;top:3px;border-left:6px solid var(--blue);border-top:3.5px solid transparent;border-bottom:3.5px solid transparent}
.social{width:32px;height:32px;border-radius:50%;background:var(--white)}
.ci{width:32px;height:32px;border-radius:50%;background:var(--white);display:flex;align-items:center;justify-content:center}
</style>
</head>
<body>

<header class="abs topbar">
  <div class="abs call"><svg width="13" height="13" viewBox="0 0 24 24"><path fill="#1a12e0" d="M6.6 10.8a15 15 0 006.6 6.6l2.2-2.2a1 1 0 011-.25 11.4 11.4 0 003.6.57 1 1 0 011 1V20a1 1 0 01-1 1A17 17 0 013 4a1 1 0 011-1h3.5a1 1 0 011 1c0 1.25.2 2.45.57 3.6a1 1 0 01-.25 1z"/></svg>Call : +1 555 014 2290</div>
  <div class="abs mail"><svg width="14" height="11" viewBox="0 0 24 18"><rect width="24" height="18" rx="2" fill="#1a12e0"/><path d="M1 2l11 8 11-8" stroke="#fff" stroke-width="2" fill="none"/></svg>Email : info@quenmirarental.com</div>
</header>

<nav class="abs nav">
  <a style="left:114px">Home</a><a style="left:220px">About</a><a style="left:326px">Services</a>
  <a style="left:765px">Vehicles</a><a style="left:888px">Reviews</a>
  <a class="cta">Contact Us</a>
</nav>
<div class="abs brand"><span>Quenmira Vehicle Rental</span></div>

<section class="abs hero" role="img" aria-label="Algarve coastline with sea stacks, waves and golden beach"></section>
<form class="abs reserve">
  <h2>Make a Reservation</h2>
  <label style="top:88px">Pick Up Location</label>
  <div class="field sel" style="left:18px;top:118px;width:313px">Please Choose......</div>
  <div class="same">Pick Up location same as return location</div>
  <label style="top:206px">Driver's age</label>
  <div class="field sel" style="left:18px;top:237px;width:313px">Please Choose......</div>
  <label style="top:294px">Vehicle Category</label>
  <div class="field sel" style="left:18px;top:324px;width:313px">All</div>
  <label style="top:386px">Pick up date</label><label style="top:386px;left:183px">Hour</label>
  <div class="field" style="left:18px;top:415px;width:145px">dd-mm-aaaa</div>
  <div class="field sel" style="left:183px;top:415px;width:146px">9.00</div>
  <label style="top:473px">Drop Off date</label><label style="top:473px;left:183px">Hour</label>
  <div class="field" style="left:18px;top:502px;width:145px">dd-mm-aaaa</div>
  <div class="field sel" style="left:183px;top:502px;width:146px">9.00</div>
  <div class="search">Search</div>
</form>
<div class="abs welcome">
  <div class="pre">WELCOME TO</div>
  <h1>QUENMIRA VEHICLE RENTAL</h1>
  <p>Itaque earum rerum hic tenetur a sapiente delectus, ut aut<br>reiciendis voluptatibus maiores alias consequatur aut perferen-<br>dis doloribus asperiores repellat.</p>
  <span class="btn">CONTACT US</span>
</div>
<div class="abs fleetshot" role="img" aria-label="White passenger van beside a blue SUV"></div>

<section class="about">
  <h2 class="abs title" style="top:884px">ABOUT QUENMIRA <em>VEHICLE RENTAL</em></h2>
  <p class="abs" style="top:940px">At vero eos et accusamus et iusto odio dignissimos ducimus qui blanditiis praesentium voluptatum deleniti atque corrupti quos dolores et quas molestias excepturi sint occaecati cupiditate non provident, similique sunt in culpa qui officia deserunt mollitia animi, id est laborum et dolorum fuga. Nam libero tempore, cum soluta nobis est eligendi optio cumque nihil impedit quo minus id quod maxime placeat facere possimus, omnis voluptas assumenda est, omnis dolor repellendus.</p>
  <p class="abs" style="top:1094px">Temporibus autem quibusdam et aut officiis debitis aut rerum necessitatibus saepe eveniet ut et voluptates repudiandae sint et molesti-ae non recusandae. Itaque earum rerum hic tenetur a sapiente delectus, ut aut reiciendis voluptatibus maiores alias consequatur aut perferendis doloribus asperiores repellat.</p>
  <div class="abs pill" style="left:515px;top:1209px;width:171px;height:51px;line-height:51px">READ MORE</div>
</section>

<section class="abs vehicles"></section>
<h2 class="abs title" style="top:1372px">OUR <em>VEHICLE</em></h2>
<div class="abs arrow" style="left:46px">‹</div>
<div class="abs arrow" style="left:1127px">›</div>
<article class="abs card" style="left:111px"><div class="ph" role="img" aria-label="White SUV driving on a country road" style="background:linear-gradient(180deg,#9aa3a8,#c9cccb 55%,#7d7f78)"></div><h3>Temporibus autem</h3></article>
<article class="abs card" style="left:455px"><div class="ph" role="img" aria-label="Blue car at sunset" style="background:linear-gradient(135deg,#f3a21c,#c5620e 45%,#1f5d8e 70%,#10304e)"></div><h3>Itaque earum rerum</h3></article>
<article class="abs card" style="left:796px"><div class="ph" role="img" aria-label="Red car on a forest road" style="background:linear-gradient(180deg,#4f6b37,#7f9a4f 45%,#8c8e8a 70%,#b7b7b2)"></div><h3>Sapiente delectus</h3></article>

<h2 class="abs title" style="top:1861px">WHAT CUSTOMER <em>SAYS</em></h2>
<div class="abs avatar" role="img" aria-label="Customer portrait" style="left:138px;top:2008px;width:66px;height:66px;background:#e2b79a"></div>
<div class="abs avatar" role="img" aria-label="Customer portrait" style="left:1014px;top:1933px;width:48px;height:48px;background:#8c7568"></div>
<div class="abs avatar" role="img" aria-label="Featured customer portrait" style="left:543px;top:1934px;width:133px;height:133px;background:#f3c9ad"></div>
<div class="abs" style="left:382px;top:2045px;width:13px;height:13px;border-radius:50%;background:var(--red)"></div>
<div class="abs" style="left:898px;top:2008px;width:6px;height:6px;border-radius:50%;background:var(--blue)"></div>
<div class="abs quote" style="left:166px;top:2066px">“</div>
<div class="abs quote" style="left:958px;top:2166px">”</div>
<div class="abs testi" style="top:2088px;font-size:21px;font-weight:600">Tomas Verlani</div>
<div class="abs testi" style="top:2126px;font-size:12px;font-weight:500;color:#555">United States</div>
<div class="abs testi" style="top:2154px;font-size:30px;color:#f2b418;letter-spacing:-2px">★★★★★</div>
<div class="abs testi" style="top:2203px;font-size:15px;font-weight:300;line-height:26px;color:#333">Itaque earum rerum hic tenetur a sapiente delectus, ut aut reiciendis voluptatibus maiores alias.<br>Consequatur aut perferendis doloribus asperiores repellat.Et harum quidem<br>rerum facilis est et expedita distinctio.</div>
<svg class="abs" style="left:540px;top:2322px" width="120" height="16"><g fill="#d6dbf2"><circle cx="8" cy="8" r="6"/><circle cx="29" cy="8" r="6"/><circle cx="50" cy="8" r="6"/><circle cx="91" cy="8" r="6"/><circle cx="112" cy="8" r="6"/></g><circle cx="70" cy="8" r="6" fill="#c8362e"/></svg>

<footer class="abs footer">
  <div class="abs" style="left:184px;top:77px;width:130px;height:130px;border-radius:50%;border:2px solid #fff;display:flex;align-items:center;justify-content:center;text-align:center;font-weight:600;font-size:18px;line-height:1.2">Quenmira Vehicle Rental</div>
  <div class="abs social" style="left:146px;top:236px" aria-label="Social profile"></div>
  <div class="abs social" style="left:204px;top:236px" aria-label="Social profile"></div>
  <div class="abs social" style="left:262px;top:236px" aria-label="Social profile"></div>
  <div class="abs social" style="left:319px;top:236px" aria-label="Social profile"></div>
  <h4 style="left:438px;top:67px">QUICK LINKS</h4>
  <ul style="left:438px;top:115px"><li><i class="dot"></i>Home</li><li><i class="dot"></i>About</li><li><i class="dot"></i>Vehicle</li><li><i class="dot"></i>Testimonials</li><li><i class="dot"></i>Contact Us</li></ul>
  <h4 style="left:662px;top:67px">HELP LINKS</h4>
  <ul style="left:662px;top:115px"><li><i class="dot"></i>FAQ</li><li><i class="dot"></i>Terms of use</li><li><i class="dot"></i>Privacy Policy</li><li><i class="dot"></i>Support Links</li><li><i class="dot"></i>Conditions</li></ul>
  <h4 style="left:896px;top:67px">CONTACT US</h4>
  <div class="abs ci" style="left:896px;top:114px"><svg width="14" height="18" viewBox="0 0 14 18"><path d="M7 0a7 7 0 017 7c0 5-7 11-7 11S0 12 0 7a7 7 0 017-7z" fill="#1a12e0"/><circle cx="7" cy="7" r="2.5" fill="#fff"/></svg></div>
  <div class="abs" style="left:940px;top:112px;font-size:15px;line-height:27px">Quenmira<br>United States</div>
  <div class="abs ci" style="left:896px;top:181px"><svg width="16" height="16" viewBox="0 0 24 24"><path fill="#1a12e0" d="M6.6 10.8a15 15 0 006.6 6.6l2.2-2.2a1 1 0 011-.25 11.4 11.4 0 003.6.57 1 1 0 011 1V20a1 1 0 01-1 1A17 17 0 013 4a1 1 0 011-1h3.5a1 1 0 011 1c0 1.25.2 2.45.57 3.6a1 1 0 01-.25 1z"/></svg></div>
  <div class="abs" style="left:940px;top:186px;font-size:15px">+1 555 014 2290</div>
  <div class="abs ci" style="left:896px;top:233px"><svg width="16" height="12" viewBox="0 0 24 18"><rect width="24" height="18" rx="2" fill="#1a12e0"/><path d="M1 2l11 8 11-8" stroke="#fff" stroke-width="2" fill="none"/></svg></div>
  <div class="abs" style="left:940px;top:238px;font-size:15px">hello@quenmirarental.com</div>
  <div class="abs" style="left:111px;top:334px;width:978px;height:1px;background:rgba(255,255,255,.7)"></div>
  <div class="abs" style="left:0;width:1200px;top:370px;text-align:center;font-size:16px;font-weight:500">Copyrights@2024.Quenmira.All Rights Reserved</div>
</footer>

</body>
</html>
```